Trabworth Business Cards

We need a business card design for Trabworth Mining.

This is a B2B company that buys and sells large machinery tires within the coal mining industry. The design should the strong, crisp and masculine. I have uploaded the company logo and rough mock-up of what the back of the card should look like. the front of the card should have the same look/feel as the back. I need editable templates for both the front and the back of the card.

Color scheme should be grey/green/black

Contact information to include on the card:
Name: Dale Pembrose
Title: Managing Director
Phone: 555-314-2069
Address: 1187 Welford #3 Dallas, TX 75290
Email: Dale@Trabworth-example.com

I am also opening a contest for letterhead design. If you submit a business card design, please also submit a letterhead design with the same look/feel. The winner of the business card design will also will the letter head and be paid for both.

Target Market(s)

Procurement men/women in the coal mining industry

Industry/Entity Type

Coal Mining

```html
<!DOCTYPE html>
<html lang="en">
<head>
<meta charset="utf-8">
<title>Trabworth Business Cards</title>
<link rel="stylesheet" href="https://fonts.googleapis.com/css2?family=Open+Sans:wght@400;600;700&display=swap">
<style>
  :root {
    --bg: #d8d3ca;
    --card: #0b0b0b;
    --green: #6ab641;
    --white: #ffffff;
    --grey: #d6d6d6;
  }
  * { margin: 0; padding: 0; box-sizing: border-box; }
  html, body { width: 1200px; height: 1024px; overflow: hidden; }
  body {
    background: var(--bg);
    font-family: "Open Sans", Arial, sans-serif;
    position: relative;
  }
  .card {
    position: absolute;
    width: 620px;
    height: 354px;
    background: var(--card);
    overflow: hidden;
    box-shadow: 0 10px 24px rgba(0,0,0,0.25);
  }
  .card-front { left: 290px; top: 110px; }
  .card-back  { left: 290px; top: 560px; }

  .card-bands { position: absolute; inset: 0; width: 620px; height: 354px; }

  .brand {
    position: absolute;
    left: 42px;
    top: 92px;
    display: flex;
    align-items: center;
    gap: 12px;
  }
  .brand-mark {
    width: 30px; height: 30px;
    background: var(--green);
  }
  .brand-name {
    color: var(--white);
    font-weight: 700;
    font-size: 30px;
    letter-spacing: 1px;
    line-height: 1;
  }
  .brand-sub {
    position: absolute;
    left: 84px;
    top: 128px;
    color: var(--green);
    font-size: 10px;
    font-weight: 600;
    letter-spacing: 15px;
  }

  .person { position: absolute; left: 42px; top: 180px; }
  .person-name { color: var(--white); font-size: 22px; font-weight: 600; line-height: 1.2; }
  .person-title { color: var(--green); font-size: 14px; line-height: 1.4; }

  .contact {
    position: absolute; left: 42px; top: 252px;
    list-style: none;
    color: var(--grey);
    font-size: 13px;
    line-height: 1.6;
  }
  .contact-label { color: var(--green); }

  .back-brand {
    position: absolute;
    left: 0; top: 0; width: 560px; height: 354px;
    display: flex; align-items: center; justify-content: center; gap: 16px;
  }
  .back-brand .brand-mark { width: 40px; height: 40px; }
  .back-brand .brand-name { font-size: 46px; }
</style>
</head>
<body>

  <section class="card card-front">
    <svg class="card-bands" viewBox="0 0 620 354" aria-hidden="true">
      <path d="M586 0 H620 V122 H602 Q586 122 586 106 Z" fill="var(--white)"/>
      <path d="M562 136 Q562 126 572 126 H584 V354 H562 Z" fill="var(--green)"/>
    </svg>
    <div class="brand">
      <span class="brand-mark"></span>
      <span class="brand-name">TRABWORTH</span>
    </div>
    <div class="brand-sub">MINING</div>
    <div class="person">
      <p class="person-name">Dale Pembrose</p>
      <p class="person-title">Managing Director</p>
    </div>
    <ul class="contact">
      <li><span class="contact-label">P:</span> 555-314-2069</li>
      <li><span class="contact-label">A:</span> 1187 Welford #3 Dallas, TX 75290</li>
      <li><span class="contact-label">E:</span> Dale@Trabworth-example.com</li>
    </ul>
  </section>

  <section class="card card-back">
    <svg class="card-bands" viewBox="0 0 620 354" aria-hidden="true">
      <path d="M586 0 H620 V122 H602 Q586 122 586 106 Z" fill="var(--white)"/>
      <path d="M562 136 Q562 126 572 126 H584 V354 H562 Z" fill="var(--green)"/>
    </svg>
    <div class="back-brand">
      <span class="brand-mark"></span>
      <span class="brand-name">TRABWORTH</span>
    </div>
  </section>

</body>
</html>
```